Web design for a honey company

We are a honey retailing company currently looking for creative design for 3 pages of our existing e-commerce website which can be found here www.alpha.tolvenmarsk.co.nz. The designs need to be responsive i.e. presented in both desktop and mobile versions. We want to use the existing page color pallet, however any fonts can be used. Please use the texts and graphic content in the attachment files provided. For more detailed instructions please. The page does not require coding, the output files should be provided as layered and editable PSD.<br/><br/>Task 2: design 2 home page banners. Images, texts and the concept provided in the "layout structure" file. <br/><br/>The web designs should be presented in both desktop and mobile versions. We are looking for professional designer submissions only!

Target Market(s)

Hi-end consumers
Health conscious consumers

Number of Pages Required

3 page

Requirements
Must have
• 50% of images supplied along + any suggested stock images.
• Supplied texts integrated in the designs.
• Please only use the product images we have provided!
Should not have
• Clipart vector bees, vector honey slots or combs.
• No images of honey in glass jars!
• Do not use images of the traditional honey wooden spoons!
• Do not use images of any other but Manuka flower!

```html
<!DOCTYPE html>
<html lang="en">
<head>
<meta charset="utf-8">
<title>Tolvenmarsk – About us (desktop and mobile)</title>
<link href="https://fonts.googleapis.com/css2?family=Tinos&family=Lato:wght@400;700&display=swap" rel="stylesheet">
<style>
:root{
  --stage:#a7a7a7;
  --ink:#1d1d1d;
  --night:#0b0d14;
  --footer:#1a1a1a;
  --paper:#f4f4f4;
  --white:#ffffff;
  --gold:#e9c36a;
  --gold-deep:#c79a3c;
  --gold-light:#f6dc8e;
  --login:#e0b24a;
}
*{box-sizing:border-box;margin:0;padding:0}
html,body{width:928px;height:1200px;overflow:hidden;background:var(--stage)}
body{position:relative;font-family:'Lato',sans-serif;color:var(--ink)}
.artboard{position:absolute;top:53px;background:var(--white);overflow:hidden}
.desktop{left:167px;width:377px;height:957px}
.mobile{left:607px;width:134px;height:1089px}
.abs{position:absolute}
.band{position:absolute;left:0;right:0}
.gold-rule{position:absolute;left:0;right:0;background:linear-gradient(90deg,var(--gold-deep),var(--gold-light) 50%,var(--gold-deep))}
.header{background:var(--night)}
.nav-link{position:absolute;color:var(--white);font-size:3.9px;white-space:nowrap}
.nav-link::after{content:" ▾";font-size:2.6px}
.brand{position:absolute;color:var(--gold);font-family:'Tinos',serif;letter-spacing:.08em;white-space:nowrap;transform:translateX(-50%)}
.account{position:absolute;display:flex;align-items:center;gap:4px}
.login{color:var(--login);font-size:3.3px;display:flex;align-items:center;gap:1px}
.hero{background:linear-gradient(180deg,#6c7a57 0%,#5d6b73 35%,#5f6f86 60%,#4f6035 100%)}
.hero-title{position:absolute;left:0;right:0;text-align:center;color:var(--white);font-family:'Tinos',serif}
.paper{background:var(--paper)}
.heading{position:absolute;font-family:'Tinos',serif;font-weight:400;color:var(--ink);white-space:nowrap;letter-spacing:.02em}
.heading.light{color:var(--white)}
.bee-mark{position:absolute;width:8px;height:5px;background:var(--gold);border-radius:2px}
.copy{position:absolute;color:#333}
.copy p+p{margin-top:1em}
.copy.light{color:var(--white)}
.frame{position:absolute;background:linear-gradient(135deg,var(--gold-light),var(--gold) 60%,var(--gold-deep))}
.photo{position:absolute}
.photo.field{background:linear-gradient(180deg,#6f9a45 0%,#88b257 45%,#9ab0c0 62%,#6e9a3a 80%,#5b8a32 100%)}
.photo.frame-held{background:linear-gradient(160deg,#4d8fb0 0%,#6b5a3a 35%,#8a6a2e 55%,#4b4030 75%,#6aa0be 100%)}
.mountains{background:linear-gradient(180deg,#5a5b5e 0%,#3e3f42 45%,#3a3426 80%,#2b2b2c 100%)}
.card{position:absolute;background:var(--white);box-shadow:0 1px 3px rgba(0,0,0,.2);padding:5px}
.card .art{width:100%;height:100%;border-radius:2px}
.art.kotare{background:linear-gradient(150deg,#1d9ad6,#3bb7e8 50%,#d07a2a)}
.art.kereru{background:linear-gradient(160deg,#9ad3c0,#6b3d8a 55%,#3a2a6a)}
.art.pukeko{background:linear-gradient(170deg,#2b2f8f,#4b3fb0 60%,#e89aa0)}
.art.tui{background:linear-gradient(150deg,#1f8f9a,#2b4f8a 60%,#f1b820)}
.bird-name{position:absolute;text-align:center;font-family:'Tinos',serif;letter-spacing:.04em;transform:translateX(-50%)}
.bird-copy{position:absolute;text-align:center;color:#444;transform:translateX(-50%);overflow:hidden}
.footer{background:var(--footer)}
.foot-links{position:absolute;color:var(--white);list-style:none}
.pay{position:absolute;display:flex;gap:2px}
.pay span{display:block;border-radius:1px}
.pay .p1{background:#1f3f8f}
.pay .p2{background:#e25a1c;border-radius:50%}
.pay .p3{background:#f0f0f0;border-bottom:2px solid #e8a42a}
.copyright{position:absolute;left:0;right:0;text-align:center;color:var(--white)}
/* desktop type */
.desktop .copy{font-size:3.75px;line-height:5.6px}
.desktop .heading{font-size:8.6px}
.desktop .bird-name{font-size:7.6px;width:70px}
.desktop .bird-copy{font-size:3.75px;line-height:5.6px;width:64px;height:56px}
.desktop .foot-links{font-size:3.3px;line-height:7px}
.desktop .copyright{font-size:3.3px}
/* mobile type */
.mobile .copy{font-size:2.5px;line-height:3.7px}
.mobile .heading{font-size:6.6px}
.mobile .bird-name{font-size:6px;width:56px}
.mobile .bird-copy{font-size:2.5px;line-height:3.6px;width:50px;height:44px}
.mobile .foot-links{font-size:2.4px;line-height:5.4px;left:0;right:0;text-align:center}
.mobile .copyright{font-size:2.4px}
</style>
</head>
<body>

<!-- DESKTOP -->
<section class="artboard desktop" aria-label="About us page, desktop">
  <header class="band header" style="top:0;height:24px">
    <span class="nav-link" style="left:89px;top:12px">Shop</span>
    <span class="nav-link" style="left:111px;top:12px">MGO Manuka honey</span>
    <span class="nav-link" style="left:227px;top:12px">About us</span>
    <span class="nav-link" style="left:257px;top:12px">Contact us</span>
    <span class="brand" style="left:188px;top:9px;font-size:7px">TOLVENMARSK</span>
    <div class="account" style="left:303px;top:2px">
      <span class="login"><svg width="5" height="5" viewBox="0 0 10 10" fill="none" stroke="#fff" stroke-width="1"><circle cx="5" cy="3" r="2.2"/><path d="M1 9.5c0-2.5 2-4 4-4s4 1.5 4 4"/></svg>Login</span>
      <svg width="6" height="5" viewBox="0 0 12 10" fill="none" stroke="#fff" stroke-width="1"><path d="M6 9.5L1.3 4.8A2.6 2.6 0 0 1 6 1.8a2.6 2.6 0 0 1 4.7 3Z"/></svg>
      <svg width="6" height="6" viewBox="0 0 12 12" fill="none" stroke="#fff" stroke-width="1"><path d="M.5 1h2l1.5 7h6l1.5-5H3.3"/><circle cx="4.5" cy="10.5" r=".8"/><circle cx="9" cy="10.5" r=".8"/></svg>
    </div>
  </header>
  <div class="gold-rule" style="top:24px;height:2px"></div>
  <div class="band hero" style="top:26px;height:124px" role="img" aria-label="Row of painted beehives on a green pasture"></div>
  <h1 class="hero-title" style="top:79px;font-size:15px;font-weight:400">ABOUT US</h1>
  <div class="gold-rule" style="top:150px;height:3px"></div>

  <section class="band paper" style="top:153px;height:173px">
    <h2 class="heading" style="left:31px;top:37px">OUR STORY</h2>
    <div class="bee-mark" role="img" aria-label="Small gold bee emblem" style="left:32px;top:52px"></div>
    <div class="copy" style="left:31px;top:68px;width:156px">
      <p>At Tolvenmarsk, we're passionate about sharing the wonders of New Zealand's honey with our discerning customers around the world. Our company was founded on the principles of providing great products with great service in an environmentally responsible way.</p>
      <p>Our honey is gathered from hives in the most pristine areas of New Zealand, with minimal processing and impact to the nature. Honey is extracted from the hives in a way to ensure minimal disruption to the bees, and processed with no additives – with honey this good, we don't need them.</p>
      <p>Along with producing great quality products, our team is also focused on providing our customers with great service. New Zealanders are known for their exceptional service skills, and we're proud to put these to use for our customers around the world.</p>
    </div>
    <div class="frame" style="left:214px;top:36px;width:130px;height:106px"></div>
    <div class="photo field" style="left:201px;top:40px;width:138px;height:106px" role="img" aria-label="Two beekeepers in white suits tending hives in a field"></div>
  </section>

  <section class="band" style="top:326px;height:225px;background:var(--white)">
    <div class="frame" style="left:45px;top:30px;width:124px;height:157px"></div>
    <div class="photo frame-held" style="left:33px;top:36px;width:133px;height:155px" role="img" aria-label="Gloved hands holding a honeycomb frame covered in bees"></div>
    <h2 class="heading" style="left:188px;top:50px">OUR PHILOSOPHY</h2>
    <h2 class="heading" style="left:188px;top:64px">THE NATURAL WAY.</h2>
    <div class="bee-mark" role="img" aria-label="Small gold bee emblem" style="left:189px;top:81px"></div>
    <div class="copy" style="left:188px;top:96px;width:158px">
      <p>Here at Tolvenmarsk, we work as hard as our bees to make sure that the honey you get is exactly as it was when the bees finished making it and sealed it in its honeycomb cell.</p>
      <p>And to ensure that we can provide you with the best honey, we need to make sure that our bees, and the environment they live in, are protected. Bees are a vital part of our ecosystem – without them, humanity may not survive. So it's no exaggeration when we say that the bees are the most important part of our business, and that we make sure that they are placed in the best environments with the best beekeepers to look after them.</p>
      <p>Tolvenmarsk Honey is made by nature and harvested for you. Nothing added, nothing taken away. Just 100% natural Manuka honey.</p>
    </div>
  </section>

  <div class="gold-rule" style="top:551px;height:3px"></div>
  <section class="band mountains" style="top:554px;height:151px" role="img" aria-label="Moody mountain range under grey cloud"></section>
  <h2 class="heading light" style="left:33px;top:577px">OUR LABELS (THE BIRDS)</h2>
  <div class="bee-mark" role="img" aria-label="Small gold bee emblem" style="left:34px;top:592px"></div>
  <div class="copy light" style="left:33px;top:608px;width:310px">
    <p>New Zealand's natural environment is like no other. As well as having unique plants, like the Manuka tree, we also have many beautiful native birds. We're proud to share our honey with the world in jars adorned by some of these birds.</p>
    <p>They're drawn by artist Maren Vostrick, who is known by the name LittleFern. Maren grew up in rural New Zealand and her artwork reflects her love of nature, simplicity and colour.</p>
  </div>
  <div class="gold-rule" style="top:705px;height:2px"></div>
  <section class="band paper" style="top:707px;height:149px"></section>

  <div class="card" style="left:40px;top:663px;width:63px;height:63px"><div class="art kotare" role="img" aria-label="Geometric illustration of a kōtare kingfisher on a branch"></div></div>
  <div class="card" style="left:118px;top:663px;width:63px;height:63px"><div class="art kereru" role="img" aria-label="Geometric illustration of a kererū wood pigeon"></div></div>
  <div class="card" style="left:196px;top:663px;width:63px;height:63px"><div class="art pukeko" role="img" aria-label="Geometric illustration of a pūkeko"></div></div>
  <div class="card" style="left:274px;top:663px;width:63px;height:63px"><div class="art tui" role="img" aria-label="Geometric illustration of a tūī on a flowering branch"></div></div>

  <h3 class="bird-name" style="left:71px;top:747px;font-weight:400">KŌTARE</h3>
  <h3 class="bird-name" style="left:149px;top:747px;font-weight:400">KERERŪ</h3>
  <h3 class="bird-name" style="left:228px;top:747px;font-weight:400">PŪKEKO</h3>
  <h3 class="bird-name" style="left:306px;top:747px;font-weight:400">TŪĪ</h3>
  <p class="bird-copy" style="left:71px;top:763px;height:40px">The kōtare is our native kingfisher and appears on our Manuka honey label. You'll see their beautiful green/blue feathers shine in the sunlight as they sit on a branch waiting for their next meal. They live all over New</p>
  <p class="bird-copy" style="left:149px;top:763px">The kererū is a wood pigeon, also known as a kūkū or kūkupa. They're only found in New Zealand and you'll see them on our rewarewa honey jars. If you're in the forest, you may hear them before you see them, with their heavy wing beats. But you'll be dazzled by their beautiful, colourful plummage when you do</p>
  <p class="bird-copy" style="left:228px;top:763px">The pūkeko can be found all over New Zealand and looks great on our Manuka blend honey. Their brilliant red beaks and frontal shields (the bit on the top of their heads), along with their big feet, long legs and purple chest make them striking characters. They're also known by the less glamourous name of the purple</p>
  <p class="bird-copy" style="left:306px;top:763px">Tūī are much like our honey bees - they love the nectar from our native flowers. You'll recognise tūī by the bright white tuft on their chest. From a distance, the rest of their plummage looks black but if you look closer, you'll find it's got a beautiful green/blue sheen to it. As a lover of many different nectars, it's only right for the tūī</p>

  <div class="gold-rule" style="top:856px;height:3px"></div>
  <footer class="band footer" style="top:859px;height:98px">
    <span class="brand" style="left:113px;top:29px;font-size:8px">TOLVENMARSK</span>
    <ul class="foot-links" style="left:187px;top:25px">
      <li>Shop</li><li>Terms &amp; Conditions</li><li>Privacy Policy</li>
    </ul>
    <ul class="foot-links" style="left:237px;top:25px">
      <li>FAQs</li><li>Partnership enquiries</li>
    </ul>
    <div class="pay" style="left:188px;top:60px" aria-label="Accepted payment methods">
      <span class="p1" style="width:34px;height:11px"></span>
      <span class="p2" style="width:11px;height:11px"></span>
      <span class="p3" style="width:19px;height:11px"></span>
    </div>
    <p class="copyright" style="top:80px">Copyright © 2020 Marskhealth Limited. All Right Reserved.</p>
  </footer>
</section>

<!-- MOBILE -->
<section class="artboard mobile" aria-label="About us page, mobile">
  <header class="band header" style="top:0;height:14px">
    <svg class="abs" style="left:7px;top:5px" width="6" height="4" viewBox="0 0 6 4" stroke="#fff" stroke-width=".6"><path d="M0 .5h6M0 2h6M0 3.5h4"/></svg>
    <span class="brand" style="left:67px;top:4px;font-size:5px">TOLVENMARSK</span>
    <div class="account" style="left:96px;top:4.5px;gap:3px">
      <span class="login" style="font-size:2.6px"><svg width="4" height="4" viewBox="0 0 10 10" fill="none" stroke="#fff" stroke-width="1"><circle cx="5" cy="3" r="2.2"/><path d="M1 9.5c0-2.5 2-4 4-4s4 1.5 4 4"/></svg>Login</span>
      <svg width="4.5" height="4" viewBox="0 0 12 10" fill="none" stroke="#fff" stroke-width="1"><path d="M6 9.5L1.3 4.8A2.6 2.6 0 0 1 6 1.8a2.6 2.6 0 0 1 4.7 3Z"/></svg>
      <svg width="4.5" height="4.5" viewBox="0 0 12 12" fill="none" stroke="#fff" stroke-width="1"><path d="M.5 1h2l1.5 7h6l1.5-5H3.3"/><circle cx="4.5" cy="10.5" r=".8"/><circle cx="9" cy="10.5" r=".8"/></svg>
    </div>
  </header>
  <div class="gold-rule" style="top:14px;height:1.5px"></div>
  <div class="band hero" style="top:15.5px;height:95.5px" role="img" aria-label="Row of painted beehives on a green pasture"></div>
  <h1 class="hero-title" style="top:52px;font-size:11px;font-weight:400">ABOUT US</h1>
  <div class="gold-rule" style="top:111px;height:2px"></div>

  <section class="band paper" style="top:113px;height:208px">
    <div class="frame" style="left:25px;top:10px;width:98px;height:78px"></div>
    <div class="photo field" style="left:14px;top:13px;width:106px;height:82px" role="img" aria-label="Two beekeepers in white suits tending hives in a field"></div>
    <h2 class="heading" style="left:7px;top:106px">OUR STORY</h2>
    <div class="bee-mark" role="img" aria-label="Small gold bee emblem" style="left:7px;top:117px;width:6px;height:4px"></div>
    <div class="copy" style="left:7px;top:129px;width:120px">
      <p>At Tolvenmarsk, we're passionate about sharing the wonders of New Zealand's honey with our discerning customers around the world. Our company was founded on the principles of providing great products with great service in an environmentally responsible way.</p>
      <p>Our honey is gathered from hives in the most pristine areas of New Zealand, with minimal processing and impact to the nature. Honey is extracted from the hives in a way to ensure minimal disruption to the bees, and processed with no additives – with honey this good, we don't need them.</p>
      <p>Along with producing great quality products, our team is also focused on providing our customers with great service. New Zealanders are known for their exceptional service skills, and we're proud to put these to use for our customers around the world.</p>
    </div>
  </section>

  <section class="band" style="top:321px;height:274px;background:var(--white)">
    <div class="frame" style="left:26px;top:23px;width:95px;height:112px"></div>
    <div class="photo frame-held" style="left:17px;top:27px;width:100px;height:117px" role="img" aria-label="Gloved hands holding a honeycomb frame covered in bees"></div>
    <h2 class="heading" style="left:7px;top:160px">OUR PHILOSOPHY</h2>
    <h2 class="heading" style="left:7px;top:171px">THE NATURAL WAY.</h2>
    <div class="bee-mark" role="img" aria-label="Small gold bee emblem" style="left:7px;top:184px;width:6px;height:4px"></div>
    <div class="copy" style="left:7px;top:196px;width:120px">
      <p>Here at Tolvenmarsk, we work as hard as our bees to make sure that the honey you get is exactly as it was when the bees finished making it and sealed it in its honeycomb cell.</p>
      <p>And to ensure that we can provide you with the best honey, we need to make sure that our bees, and the environment they live in, are protected. Bees are a vital part of our ecosystem – without them, humanity may not survive. So it's no exaggeration when we say that the bees are the most important part of our business, and that we make sure that they are placed in the best environments with the best beekeepers to look after them.</p>
      <p>Tolvenmarsk Honey is made by nature and harvested for you. Nothing added, nothing taken away. Just 100% natural Manuka honey.</p>
    </div>
  </section>

  <div class="gold-rule" style="top:595px;height:2px"></div>
  <section class="band mountains" style="top:597px;height:113px" role="img" aria-label="Moody mountain range under grey cloud"></section>
  <h2 class="heading light" style="left:7px;top:609px">OUR LABELS (THE BIRDS)</h2>
  <div class="bee-mark" role="img" aria-label="Small gold bee emblem" style="left:7px;top:620px;width:6px;height:4px"></div>
  <div class="copy light" style="left:7px;top:631px;width:121px">
    <p>New Zealand's natural environment is like no other. As well as having unique plants, like the Manuka tree, we also have many beautiful native birds. We're proud to share our honey with the world in jars adorned by some of these birds.</p>
    <p>They're drawn by artist Maren Vostrick, who is known by the name LittleFern. Maren grew up in rural New Zealand and her artwork reflects her love of nature, simplicity and colour.<br>If you're not familiar with New Zealand's birds, here's a little bit more about those that you'll see on our jars.</p>
  </div>
  <div class="gold-rule" style="top:710px;height:2px"></div>
  <section class="band paper" style="top:712px;height:248px"></section>

  <div class="card" style="left:13px;top:686px;width:48px;height:49px;padding:4px"><div class="art kotare" role="img" aria-label="Geometric illustration of a kōtare kingfisher on a branch"></div></div>
  <div class="card" style="left:72px;top:686px;width:48px;height:49px;padding:4px"><div class="art kereru" role="img" aria-label="Geometric illustration of a kererū wood pigeon"></div></div>
  <h3 class="bird-name" style="left:37px;top:749px;font-weight:400">KŌTARE</h3>
  <h3 class="bird-name" style="left:96px;top:749px;font-weight:400">KERERŪ</h3>
  <p class="bird-copy" style="left:37px;top:762px;height:33px">The kōtare is our native kingfisher and appears on our Manuka honey label. You'll see their beautiful green/blue feathers shine in the sunlight as they sit on a branch waiting for their next meal. They live all over New</p>
  <p class="bird-copy" style="left:96px;top:760px">The kererū is a wood pigeon, also known as a kūkū or kūkupa. They're only found in New Zealand and you'll see them on our rewarewa honey jars. If you're in the forest, you may hear them before you see them, with their heavy wing beats. But you'll be dazzled by their beautiful, colourful plummage when you do</p>

  <div class="card" style="left:13px;top:820px;width:48px;height:49px;padding:4px"><div class="art pukeko" role="img" aria-label="Geometric illustration of a pūkeko"></div></div>
  <div class="card" style="left:72px;top:820px;width:48px;height:49px;padding:4px"><div class="art tui" role="img" aria-label="Geometric illustration of a tūī on a flowering branch"></div></div>
  <h3 class="bird-name" style="left:39px;top:885px;font-weight:400">PŪKEKO</h3>
  <h3 class="bird-name" style="left:97px;top:885px;font-weight:400">TŪĪ</h3>
  <p class="bird-copy" style="left:39px;top:897px">The pūkeko can be found all over New Zealand and looks great on our Manuka blend honey. Their brilliant red beaks and frontal shields (the bit on the top of their heads), along with their big feet, long legs and purple chest make them striking characters. They're also known by the less glamourous name of the purple</p>
  <p class="bird-copy" style="left:97px;top:897px">Tūī are much like our honey bees - they love the nectar from our native flowers. You'll recognise tūī by the bright white tuft on their chest. From a distance, the rest of their plummage looks black but if you look closer, you'll find it's got a beautiful green/blue sheen to it. As a lover of many different nectars, it's only right for the tūī</p>

  <div class="gold-rule" style="top:960px;height:2px"></div>
  <footer class="band footer" style="top:962px;height:127px">
    <span class="brand" style="left:67px;top:22px;font-size:7px">TOLVENMARSK</span>
    <ul class="foot-links" style="top:55px">
      <li>Shop</li><li>Terms &amp; Conditions</li><li>Privacy Policy</li>
    </ul>
    <ul class="foot-links" style="top:78px">
      <li>FAQs</li><li>Partnership enquiries</li>
    </ul>
    <div class="pay" style="left:38px;top:101px" aria-label="Accepted payment methods">
      <span class="p1" style="width:27px;height:8px"></span>
      <span class="p2" style="width:8px;height:8px"></span>
      <span class="p3" style="width:15px;height:8px"></span>
    </div>
    <p class="copyright" style="top:117px">Copyright © 2020 Marskhealth Limited. All Right Reserved.</p>
  </footer>
</section>

</body>
</html>
```